Banner Ad in Spanish for Car Accident Law Firm in Miami Florida

I need a Banner Ad in Spanish Language. We are an Accident Law Firm in Miami, FL. We help injured people. I need a Banner Ad with a Vibrant Colorful Background to Stand Out. A Click-Able Call to Action is needed. We don't want to make the banner too crowded and we want the message to be simple to understand. We are looking for a skilled graphic designer to create a visually appealing banner ad for our YouTube marketing campaign. The required dimensions and format are:
1920 x 275
.png & .mp4

The Banner is for our Plaintiff’s Personal Injury Law Firm. We represent Spanish Speaking clients who are injured in CAR ACCIDENTS. As such the banner must include:
1. Our Firm Logo
2. Our Telephone# (305) 447-2086
3. Stock Photo of Car Crash
4. Photo of our attorney in office
5. The Words Abogados de Accidentes
The telephone number should be fairly large and stand out it is our call to action. The words Abogados de Accidentes should be close to our Logo to associate the two.

Target Market(s)

Car Accident Victims who speak Spanish

Industry/Entity Type

Legal, Law Firm.

Font styles to use
Sans Serif

Colors
59FF00
82FF00
B8FF75
E3FFCB
F4FFEA
F0912C
F2A743
F7CA91
FBE8D2
FDF5EE
6B429C
8869AF
B7A5CE
E3DAEB
F3F0F8

Requirements
Must have
• A bold background so that Banner Ad can be seen on mobile and against the screen being advertising against
Should not have
• Be too crowded. Hard to understand what it is for.

```html
<!DOCTYPE html>
<html lang="es">
<head>
<meta charset="utf-8">
<title>Morvante Law Firm – Abogados de Accidentes</title>
<link rel="stylesheet" href="https://fonts.googleapis.com/css2?family=Bebas+Neue&family=Oswald:wght@600&display=swap">
<style>
  :root{
    --page:#ffffff;
    --banner-bg:#eeeeef;
    --banner-bg-light:#fafafa;
    --navy:#231d5c;
    --purple:#4a2d6e;
    --purple-deep:#3b2359;
    --orange:#ef6a0c;
    --orange-light:#f0912c;
    --white:#ffffff;
    --photo-suit-a:#8d8f95;
    --photo-suit-b:#2a2f3c;
    --photo-car-a:#9fa4ab;
    --photo-car-b:#22314f;
  }
  html,body{margin:0;padding:0;width:1200px;height:873px;overflow:hidden;background:var(--page);}
  .canvas{position:relative;width:1200px;height:873px;}
  .shapes{position:absolute;inset:0;}
  .brand{
    position:absolute;left:173px;top:378px;
    font-family:"Oswald",sans-serif;font-weight:600;color:var(--navy);
    line-height:1;letter-spacing:1px;
  }
  .brand-name{display:block;font-size:30px;}
  .brand-sub{display:block;font-size:13px;letter-spacing:2px;margin-top:6px;text-align:right;}
  .tagline{
    position:absolute;left:90px;top:449px;
    font-family:"Bebas Neue",sans-serif;font-size:32px;line-height:40px;
    color:var(--white);white-space:nowrap;
    transform:scaleX(.92);transform-origin:left center;
  }
  .cta-label{
    position:absolute;left:553px;top:369px;
    font-family:"Bebas Neue",sans-serif;font-size:40px;line-height:40px;color:var(--white);
  }
  .cta-phone{
    position:absolute;left:548px;top:424px;
    font-family:"Bebas Neue",sans-serif;font-size:80px;line-height:80px;
    color:var(--white);white-space:nowrap;text-decoration:none;
    transform:scaleX(.83);transform-origin:left center;
  }
</style>
</head>
<body>
<div class="canvas">
  <svg class="shapes" width="1200" height="873" viewBox="0 0 1200 873">
    <defs>
      <linearGradient id="bannerGrad" x1="0" y1="0" x2="1" y2="0">
        <stop offset="0" stop-color="var(--banner-bg-light)"/>
        <stop offset="1" stop-color="var(--banner-bg)"/>
      </linearGradient>
      <linearGradient id="attorneyGrad" x1="0" y1="0" x2="1" y2="1">
        <stop offset="0" stop-color="var(--photo-suit-a)"/>
        <stop offset=".6" stop-color="var(--photo-suit-b)"/>
        <stop offset="1" stop-color="#d9dde2"/>
      </linearGradient>
      <linearGradient id="carGrad" x1="0" y1="0" x2="1" y2="0">
        <stop offset="0" stop-color="var(--photo-car-a)"/>
        <stop offset=".5" stop-color="#4b5566"/>
        <stop offset="1" stop-color="var(--photo-car-b)"/>
      </linearGradient>
    </defs>

    <rect class="banner" x="57" y="356" width="1086" height="160" fill="url(#bannerGrad)"/>

    <rect class="brand-mark" x="106" y="376" width="59" height="59" rx="8" fill="var(--navy)"/>

    <polygon class="tagline-band" points="84,446 346,446 334,491 70,491" fill="var(--purple-deep)"/>

    <g role="img" aria-label="Foto del abogado en su oficina">
      <polygon points="346,367 508,367 470,507 340,507 331,497" fill="url(#attorneyGrad)"/>
    </g>

    <g role="img" aria-label="Foto de un choque entre dos autos">
      <polygon points="900,369 1143,369 1143,508 856,508" fill="url(#carGrad)"/>
    </g>

    <line class="accent-line" x1="619" y1="504" x2="860" y2="504" stroke="var(--orange-light)" stroke-width="4"/>
    <polygon class="accent-tick" points="891,369 898,369 895,381 888,381" fill="var(--orange)"/>

    <polygon class="cta-panel" points="504,373 936,373 902,501 470,501" fill="var(--purple)"/>

    <polygon class="cta-tag" points="540,369 715,369 696,410 528,410" fill="var(--orange)"/>

    <path class="phone-icon" fill="var(--white)"
      d="M500 447c3-2 6-2 7 1l6 9c1 3 0 5-2 6l-3 2c2 5 7 10 12 12l2-3c2-2 4-2 6-1l8 6c2 2 2 5 0 7l-3 3c-4 4-12 2-21-6s-14-18-12-25z"/>
  </svg>

  <div class="brand">
    <span class="brand-name">MORVANTE</span>
    <span class="brand-sub">LAW FIRM</span>
  </div>

  <div class="tagline">ABOGADOS DE ACCIDENTES</div>

  <div class="cta-label">LLAMANOS</div>
  <a class="cta-phone" href="tel:+13054472086">(305) 447-2086</a>
</div>
</body>
</html>
```